Business Card for a mobile physiotherapy company

I need a layout for a business card for a mobile physiotherapy company.
Slogan is "Mobile Physiotherapy - Your Road To Recovery"
Phone number is 867-555-0142
Email VardenTherapy@postnest.ca (subject to change with website)
Website www.VardenTherapy.ca
My name and credentials: Luke Varden Luke Varden, BSc(kin), MPT, CAFCI, IMS
Information maybe included: Direct Billing, Services including Physiotherapy, IMS, acupuncture
Maybe include facebook and instagram logos
One side with the logo clean and sharp
Other side with details, try not to look too busy, keep everything concise

```html
<!DOCTYPE html>
<html lang="en">
<head>
<meta charset="utf-8">
<title>Varden Therapy – Business Card</title>
<link href="https://fonts.googleapis.com/css2?family=Tinos:wght@400;700&display=swap" rel="stylesheet">
<style>
  :root {
    --navy: #2c4a70;
    --navy-soft: #34557e;
    --green: #0e5448;
    --ink: #555555;
    --paper: #ffffff;
    --stage: #2b2b2b;
    --rule: #6f86a6;
  }
  * { margin: 0; padding: 0; box-sizing: border-box; }
  html, body {
    width: 1125px; height: 1200px; overflow: hidden;
    background: var(--stage);
    font-family: "Tinos", "Times New Roman", serif;
  }
  .canvas { position: relative; width: 1125px; height: 1200px; }

  .card {
    position: absolute; left: 171px; width: 826px; height: 472px;
    background: var(--paper); overflow: hidden;
    box-shadow: 0 4px 10px rgba(0,0,0,.45);
  }
  .card--front { top: 106px; }
  .card--back  { top: 639px; }

  /* Front */
  .front__banner {
    position: absolute; left: 0; top: 0; width: 100%; height: 175px;
    background: linear-gradient(180deg, var(--navy) 0%, var(--navy-soft) 100%);
  }
  .holder {
    position: absolute; right: 38px; top: 28px; text-align: right; color: var(--paper);
  }
  .holder__name { font-size: 32px; font-weight: 700; letter-spacing: 1px; line-height: 1; }
  .holder__creds { font-size: 17px; font-weight: 700; margin-top: 8px; line-height: 1; }
  .holder__note { font-size: 22px; font-weight: 700; margin-top: 4px; line-height: 1.1; }

  .wordmark { position: absolute; left: 0; width: 100%; text-align: center; color: var(--green); font-weight: 700; }
  .wordmark span { display: block; line-height: 1; }
  .wordmark--front { top: 214px; }
  .wordmark--front .wordmark__main { font-size: 54px; letter-spacing: 6px; }
  .wordmark--front .wordmark__sub  { font-size: 24px; letter-spacing: 9px; margin-top: 8px; }

  .front__info { position: absolute; left: 0; top: 316px; width: 100%; text-align: center; color: var(--ink); }
  .services, .slogan { font-size: 22px; line-height: 26px; }
  .services .dot {
    display: inline-block; width: 7px; height: 7px; border-radius: 50%;
    background: var(--navy); vertical-align: middle; margin: 0 8px 0 10px;
  }
  .divider { width: 430px; height: 1px; margin: 12px auto 12px; background: linear-gradient(90deg, transparent, var(--rule), transparent); }
  .contact { font-size: 21px; line-height: 27px; }
  .contact__web { letter-spacing: 1.5px; }

  /* Back */
  .wordmark--back { top: 170px; }
  .wordmark--back .wordmark__main { font-size: 74px; letter-spacing: 7px; }
  .wordmark--back .wordmark__sub  { font-size: 33px; letter-spacing: 12px; margin-top: 14px; }

  .social { position: absolute; left: 0; top: 363px; width: 100%; display: flex; justify-content: center; align-items: center; gap: 6px; }
  .social__rule { width: 134px; height: 1px; background: var(--rule); margin: 0 10px; }
  .social__icon { width: 36px; height: 36px; border-radius: 50%; background: var(--navy); }
</style>
</head>
<body>
<main class="canvas">

  <section class="card card--front">
    <div class="front__banner" role="img" aria-label="Navy mountain range banner"></div>
    <div class="holder">
      <div class="holder__name">LUKE VARDEN</div>
      <div class="holder__creds">BSc(kin), MPT, CAFCI, IMS</div>
      <div class="holder__note">Direct Billing</div>
    </div>
    <div class="wordmark wordmark--front">
      <span class="wordmark__main">VARDEN</span>
      <span class="wordmark__sub">THERAPY</span>
    </div>
    <div class="front__info">
      <p class="services">Physiotherapy<span class="dot"></span>IMS<span class="dot"></span>Acupuncture</p>
      <p class="slogan">Mobile Physiotherapy - Your Road To Recovery</p>
      <div class="divider"></div>
      <p class="contact">867-555-0142 &nbsp;| VardenTherapy@postnest.ca</p>
      <p class="contact contact__web">www.VardenTherapy.ca</p>
    </div>
  </section>

  <section class="card card--back">
    <div class="wordmark wordmark--back">
      <span class="wordmark__main">VARDEN</span>
      <span class="wordmark__sub">THERAPY</span>
    </div>
    <div class="social">
      <span class="social__rule"></span>
      <span class="social__icon" role="img" aria-label="Social profile one"></span>
      <span class="social__icon" role="img" aria-label="Social profile two"></span>
      <span class="social__rule"></span>
    </div>
  </section>

</main>
</body>
</html>
```